Plant based protein powders and bars in different flavors need a packaging design

I need a packaging design for a new company called "Vale Verdura". We develop plant based protein powders and Bars which are made with completely organic food ingredients and are completely free of preservative and artificial additives. The aim is to create something that speaks purity, Doesn't mislead the customer and signifies Pure and natural food. Sun gives life to vegetation and that's what we use to survive. We will use both stand-up pouches and tubs to sell our powder. So I need a packaging design for both.The protein bars are something where I would like to try and be creative with the packaging. There are multiple flavors. For each flavor we need a different color theme but the overall theme should remain the same.

Target Market(s)

working individuals who are looking for too busy to eat a complete nutritious meal or lack time to make one. Target consumer needs something that they can consume anytime they want, irrespective of the place they're at. Nutrition deprived people are our target consumers.

Industry/Entity Type

Nutrition

Font styles to use
Serif
Decorative

Colors

Designer to choose colors to be used in the design.

Requirements
Must have
• Unique Eye catching packaging design. Simple yet elegant. Something that says Pure and Simple yet powerful and effective.
Should not have
• Complex packaging that makes it harder for consumers to make a buying decision.

```html
<!DOCTYPE html>
<html lang="en">
<head>
<meta charset="utf-8">
<title>Vale Verdura – Complete Plant Based Protein, Mint Chocolate</title>
<link rel="stylesheet" href="https://fonts.googleapis.com/css2?family=Cinzel:wght@700&family=Open+Sans:wght@400;600;700&display=swap">
<style>
  :root {
    --stage: #e6e7e8;
    --panel: #f7f8f8;
    --leaf: #7fb33e;
    --leaf-deep: #4d8a2a;
    --cocoa: #6b3a1f;
    --orange: #ee7a2c;
    --orange-light: #f4a95c;
    --ink: #3a3a3a;
    --badge-green: #2e9e3f;
    --brand-panel: #eceeef;
  }
  * { margin: 0; padding: 0; box-sizing: border-box; }
  html, body { width: 1200px; height: 663px; overflow: hidden; }
  body { background: var(--stage); font-family: "Open Sans", sans-serif; position: relative; }

  .pack-front {
    position: absolute; left: 425px; top: 16px; width: 350px; height: 630px;
    background: linear-gradient(180deg, #fbfbfb 0%, var(--panel) 60%, #eff0f0 100%);
    overflow: hidden; box-shadow: 0 2px 10px rgba(0,0,0,.12);
  }
  .top-band {
    position: absolute; left: 0; top: 0; width: 350px; height: 46px;
    background: linear-gradient(90deg, var(--leaf-deep) 0%, #8fae57 45%, #9a6a3a 80%, #7a3f1f 100%);
  }

  .brand-panel {
    position: absolute; left: 96px; top: 62px; width: 158px; height: 160px;
    background: var(--brand-panel); border-radius: 6px;
  }
  .brand-name {
    position: absolute; left: 0; top: 124px; width: 350px; text-align: center;
    font-family: "Open Sans", sans-serif; font-weight: 600; font-size: 19px; color: var(--ink);
  }
  .brand-dot {
    display: inline-block; width: 9px; height: 9px; border-radius: 50%;
    background: var(--ink); margin-right: 7px; vertical-align: middle;
  }

  .product-title {
    position: absolute; left: 0; top: 262px; width: 350px; text-align: center;
    font-family: "Cinzel", serif; font-weight: 700; font-size: 50px; line-height: 1;
    background: linear-gradient(90deg, #e0632a 0%, var(--orange) 45%, var(--orange-light) 100%);
    -webkit-background-clip: text; background-clip: text; color: transparent;
  }
  .product-sub {
    position: absolute; left: 0; top: 320px; width: 350px; text-align: center;
    font-weight: 700; font-size: 9.5px; letter-spacing: 4px; color: var(--ink);
  }
  .flavour-band {
    position: absolute; left: 70px; top: 340px; width: 218px; height: 32px;
    background: linear-gradient(90deg, var(--leaf) 0%, #8a6a32 55%, var(--cocoa) 100%);
    color: #fff; font-weight: 700; font-size: 23px; line-height: 32px; text-align: center;
  }
  .claim-line {
    position: absolute; left: 0; top: 378px; width: 350px; text-align: center;
    font-weight: 600; font-size: 5.6px; color: var(--ink);
  }
  .claim-line .sep { color: var(--orange); margin: 0 3px; }

  .macro-row { position: absolute; left: 0; top: 394px; width: 350px; display: flex; justify-content: center; gap: 9px; }
  .macro {
    width: 25px; height: 25px; border-radius: 50%; background: var(--badge-green);
    color: #fff; text-align: center; font-weight: 700; font-size: 7.5px; line-height: 1;
    padding-top: 5px;
  }
  .macro small { display: block; font-size: 4.5px; font-weight: 600; margin-top: 2px; }

  .flavour-art {
    position: absolute; left: 104px; top: 434px; width: 150px; height: 120px; border-radius: 50%;
    background: radial-gradient(ellipse at 55% 40%, #9ccf6a 0%, #cfe2bd 35%, #a7774f 70%, #eef0ef 100%);
  }

  .additive-seal {
    position: absolute; left: 36px; top: 497px; width: 56px; height: 56px; border-radius: 50%;
    border: 2px solid var(--orange); color: var(--orange); text-align: center;
    font-size: 7px; line-height: 1.3; padding-top: 12px;
  }
  .free-list { position: absolute; left: 266px; top: 490px; list-style: none; }
  .free-list li {
    font-size: 6.5px; color: var(--badge-green); margin-bottom: 9px;
    display: flex; align-items: center; gap: 4px;
  }
  .free-list .icon { width: 9px; height: 9px; border-radius: 50%; border: 1.3px solid var(--orange); }

  .hex-field {
    position: absolute; left: 0; top: 556px; width: 350px; height: 54px;
    background: linear-gradient(180deg, rgba(244,169,92,0) 0%, rgba(244,169,92,.35) 100%);
  }
  .base-band {
    position: absolute; left: 0; bottom: 0; width: 350px; height: 20px;
    background: linear-gradient(90deg, var(--leaf-deep) 0%, var(--leaf) 30%, #8a6a32 70%, var(--cocoa) 100%);
  }
  .net-weight {
    position: absolute; left: 146px; top: 564px; width: 62px; height: 66px;
    background: linear-gradient(180deg, #7a5a2a, var(--cocoa));
    color: #fff; text-align: center; font-size: 6px; line-height: 1.6; padding-top: 9px;
  }
  .net-weight hr { border: 0; border-top: .6px solid #fff; width: 40px; margin: 2px auto; }
  .net-weight strong { font-size: 7.5px; }
</style>
</head>
<body>
  <main class="pack-front">
    <div class="top-band" role="img" aria-label="Green to brown flowing header artwork"></div>

    <div class="brand-panel"></div>
    <p class="brand-name"><span class="brand-dot"></span>Vale Verdura</p>

    <h1 class="product-title">PROTEIN</h1>
    <p class="product-sub">COMPLETE PLANT BASED</p>
    <p class="flavour-band">MINT CHOCOLATE</p>
    <p class="claim-line">COMPLETE AMINO ACID PROFILE<span class="sep">|</span>INFUSED WITH VITAMINS AND DIGESTIVE ENZYMES</p>

    <div class="macro-row">
      <div class="macro">20G<small>Protine</small></div>
      <div class="macro">0G<small>Sugar</small></div>
      <div class="macro">3G<small>Carbs</small></div>
    </div>

    <div class="flavour-art" role="img" aria-label="Mint chocolate pieces with fresh mint leaves"></div>

    <div class="additive-seal">Free of<br>Artificial<br>Additives</div>
    <ul class="free-list">
      <li><span class="icon"></span>GLUTEN FREE</li>
      <li><span class="icon"></span>DAIRY FREE</li>
      <li><span class="icon"></span>NON-GMO</li>
    </ul>

    <div class="hex-field" role="img" aria-label="Soft orange hexagon pattern"></div>
    <div class="base-band"></div>
    <div class="net-weight">NUTRITION<br>SUPPLEMENT<hr><strong>450 GM</strong></div>
  </main>
</body>
</html>
```